Flyer for the Radiant Harvest Worship Day

I am looking to create a flyer for a one day prayer retreat our church is organizing.
This flyer will be posted on social media, websites and will also be printed so it can be mailed to people.
I am looking for something professional, with good use of our logo and band colors (logo colors).
I am counting on the designer's skill, creativity, art and knowledge of media communication to produce a flyer that will effectively and quickly convey the message we are trying to spread.
CONTENT OF THE FLYER:
Event title: Radiant Harvest Worship Day
Date: Tuesday July 2nd, 2019
Time: 11:00AM - 7:00PM
Belmora Hotel, 4875 Wexley Avenue, Portland, Maine 04102 (Room: Juniper)
Event Key words to highlight what the event is about: Prayer, Sharing the Word, Panel discussion, prophecy, Impartation.
Key phrases:
A one day prayer retreat.
Jesus Chris is Lord
Contact info:
www.tolvex.org
Phone: 207 555 3184
Email: contact@brookhavenfold.org

```html
<!DOCTYPE html>
<html lang="en">
<head>
<meta charset="utf-8">
<title>Radiant Harvest Worship Day</title>
<link href="https://fonts.googleapis.com/css2?family=Bebas+Neue&family=Arimo:wght@400;700&display=swap" rel="stylesheet">
<style>
  :root {
    --navy: #0f3a63;
    --orange: #f39a1e;
    --white: #ffffff;
    --ink: #1f2d3d;
    --sky-top: #7fa6cf;
    --sky-bottom: #e9eef3;
    --rule: #c98a3a;
  }
  * { margin: 0; padding: 0; box-sizing: border-box; }
  html, body { width: 866px; height: 1200px; overflow: hidden; background: var(--white); }
  .canvas {
    position: relative; width: 866px; height: 1200px;
    border: 1px solid #9a9a9a; background: var(--white);
    font-family: "Arimo", Arial, sans-serif;
  }
  .flyer {
    position: absolute; left: 42px; top: 47px; width: 781px; height: 1103px;
    background: var(--navy); overflow: hidden;
  }
  .top-rule { position: absolute; left: 48px; top: 31px; width: 690px; height: 2px; background: var(--white); }
  .hero {
    position: absolute; left: 0; top: 35px; width: 781px; height: 540px;
    background: linear-gradient(180deg, var(--sky-top) 0%, #b9cde2 45%, var(--sky-bottom) 100%);
  }
  .event-title { position: absolute; left: 53px; top: 88px; font-family: "Bebas Neue", sans-serif; line-height: 1; }
  .event-title .kicker { display: block; color: var(--orange); font-size: 50px; }
  .event-title .main { display: block; color: var(--navy); font-size: 66px; margin-top: 2px; }
  .brand-box {
    position: absolute; left: 507px; top: 35px; width: 233px; height: 198px; background: var(--navy);
    display: flex; align-items: center; justify-content: center; gap: 10px;
  }
  .brand-name { color: var(--white); font-family: "Arimo", Arial, sans-serif; font-size: 40px; font-weight: 400; letter-spacing: 1px; }
  .brand-dot { width: 22px; height: 22px; border-radius: 50%; background: var(--orange); }
  .tagline-band {
    position: absolute; left: 0; top: 580px; width: 781px; height: 115px; background: var(--orange);
    text-align: center;
  }
  .tagline-band .headline { font-family: "Bebas Neue", sans-serif; color: var(--white); font-size: 70px; line-height: 1; padding-top: 14px; }
  .tagline-band .sub { font-weight: 700; color: var(--ink); font-size: 24px; margin-top: 2px; }
  .keywords { position: absolute; left: 0; top: 716px; width: 781px; text-align: center; color: var(--white); font-weight: 700; font-size: 28px; line-height: 40px; }
  .details { position: absolute; top: 823px; left: 0; width: 781px; height: 150px; color: var(--white); font-size: 23px; line-height: 36px; }
  .detail { position: absolute; top: 0; }
  .detail .icon { position: absolute; left: 0; top: 0; }
  .detail.date { left: 62px; width: 190px; }
  .detail.time { left: 270px; width: 170px; }
  .detail.venue { left: 457px; width: 300px; }
  .detail p { padding-left: 42px; }
  .detail.date p, .detail.time p { text-align: right; padding-left: 0; }
  .divider { position: absolute; top: 0; width: 1px; height: 110px; background: var(--rule); }
  .bottom-rule { position: absolute; left: 33px; top: 990px; width: 715px; height: 1px; background: #8aa0b8; }
  .footer-brand { position: absolute; left: 70px; top: 1020px; display: flex; align-items: center; gap: 10px; }
  .footer-brand .brand-name { font-size: 40px; }
  .contacts { position: absolute; left: 272px; top: 1002px; color: var(--white); font-size: 28px; line-height: 40px; }
  .contacts .row { display: flex; align-items: center; gap: 10px; }
  .contacts svg { flex: none; }
</style>
</head>
<body>
<div class="canvas">
  <div class="flyer">
    <div class="top-rule"></div>
    <div class="hero" role="img" aria-label="Photo of worshippers in white raising their hands toward a bright cloudy sky"></div>

    <h1 class="event-title">
      <span class="kicker">Radiant Harvest</span>
      <span class="main">Worship Day</span>
    </h1>

    <div class="brand-box">
      <span class="brand-dot"></span>
      <span class="brand-name">TOLVEX</span>
    </div>

    <div class="tagline-band">
      <p class="headline">A One Day Prayer Retreat.</p>
      <p class="sub">JESUS CHRIS IS LORD</p>
    </div>

    <div class="keywords">
      <p>Prayer | Sharing the Word</p>
      <p>Panel discussion | Prophecy | Impartation.</p>
    </div>

    <div class="details">
      <div class="detail date">
        <svg class="icon" width="32" height="32" viewBox="0 0 32 32" aria-hidden="true">
          <circle cx="16" cy="16" r="16" fill="var(--orange)"/>
          <rect x="8" y="9" width="16" height="15" rx="2" fill="none" stroke="#fff" stroke-width="2"/>
          <line x1="8" y1="13" x2="24" y2="13" stroke="#fff" stroke-width="2"/>
          <line x1="12" y1="7" x2="12" y2="11" stroke="#fff" stroke-width="2"/>
          <line x1="20" y1="7" x2="20" y2="11" stroke="#fff" stroke-width="2"/>
        </svg>
        <p>Tuesday<br>July 2nd, 2019</p>
      </div>
      <div class="divider" style="left:255px"></div>
      <div class="detail time">
        <svg class="icon" width="32" height="32" viewBox="0 0 32 32" aria-hidden="true">
          <circle cx="16" cy="16" r="16" fill="var(--orange)"/>
          <circle cx="16" cy="16" r="8" fill="none" stroke="#fff" stroke-width="2"/>
          <polyline points="16,11 16,16 19,18" fill="none" stroke="#fff" stroke-width="2"/>
        </svg>
        <p>11:00AM<br>to 7:00PM</p>
      </div>
      <div class="divider" style="left:441px"></div>
      <div class="detail venue">
        <svg class="icon" width="32" height="32" viewBox="0 0 32 32" aria-hidden="true">
          <circle cx="16" cy="16" r="16" fill="var(--orange)"/>
          <path d="M16 25 C11 19 10 16 10 14 a6 6 0 0 1 12 0 c0 2 -1 5 -6 11z" fill="none" stroke="#fff" stroke-width="2"/>
          <circle cx="16" cy="14" r="2" fill="#fff"/>
        </svg>
        <p>Belmora Hotel,<br>4875 Wexley Avenue,<br>Portland, Maine 04102<br>&nbsp;(Room: Juniper)</p>
      </div>
    </div>

    <div class="bottom-rule"></div>

    <div class="footer-brand">
      <span class="brand-dot"></span>
      <span class="brand-name">TOLVEX</span>
    </div>

    <div class="contacts">
      <div class="row">
        <svg width="22" height="22" viewBox="0 0 22 22" aria-hidden="true">
          <circle cx="11" cy="11" r="9" fill="none" stroke="#fff" stroke-width="1.6"/>
          <ellipse cx="11" cy="11" rx="4" ry="9" fill="none" stroke="#fff" stroke-width="1.4"/>
          <line x1="2" y1="11" x2="20" y2="11" stroke="#fff" stroke-width="1.4"/>
        </svg>
        <span>tolvex.org</span>
        <svg width="28" height="22" viewBox="0 0 28 22" aria-hidden="true" style="margin-left:8px">
          <path d="M3 9 q11 -8 22 0 l-3 3 -4 -2 v-2 q-4 -1 -8 0 v2 l-4 2z" fill="none" stroke="#fff" stroke-width="1.5"/>
          <rect x="7" y="12" width="14" height="8" rx="2" fill="none" stroke="#fff" stroke-width="1.5"/>
        </svg>
        <span>207 555 3184</span>
      </div>
      <div class="row">
        <svg width="22" height="22" viewBox="0 0 22 22" aria-hidden="true">
          <rect x="2" y="5" width="18" height="12" fill="none" stroke="#fff" stroke-width="1.5"/>
          <polyline points="2,5 11,12 20,5" fill="none" stroke="#fff" stroke-width="1.5"/>
        </svg>
        <span>contact@brookhavenfold.org</span>
      </div>
    </div>
  </div>
</div>
</body>
</html>
```